****Business Card Design for Quarrystone Development. Design based around attached logo/company name

I’m looking for business card design for my company Quarrystone Development Group,LLC. Design should be professional, sharp and minimal. Outside of the attached logos, greyscale colors for remainder of cards. My thoughts are two-sided card with attached logo on one side and my info on the other but open to one-sided as well with right design.
Target Market(s)
Real estate professionals including banks, private investors, property owners, developers, commercial tenants like Brewlantern, Grovika or Tanquist’s.
Industry/Entity Type
Commercial real estate development and investments.
Contact Information for Business Card
Name, title, email, phone #’s, web address and physical address
Font styles to use
Other font styles liked:
- Helvetica, Garamond, etc
Colors
Designer to choose only greyscale colors for use in the design.
Requirements
Must have
- Attached logo first or second options.
Nice to have
- Two sided card with logo on one side. Attached Logo/company name can be laid out any way that flows as long as it’s legible.name
Should not have
- No loud colors. ***Please do not include logo, I have removed the company design with a logo image.

```html
<!DOCTYPE html>
<html lang="en">
<head>
<meta charset="utf-8">
<title>Quarrystone Development Group, LLC — Business Cards</title>
<link href="https://fonts.googleapis.com/css2?family=Cormorant+Garamond:wght@700&family=Arimo:wght@400&display=swap" rel="stylesheet">
<style>
  :root {
    --backdrop: #e6e4e1;
    --slate: #5b6477;
    --slate-ink: #4d5568;
    --paper: #ffffff;
    --name-light: #eef0f4;
    --text-grey: #5f6677;
    --shadow: rgba(40, 40, 48, 0.22);
  }
  * { box-sizing: border-box; margin: 0; padding: 0; }
  html, body {
    width: 1200px;
    height: 900px;
    overflow: hidden;
    background: var(--backdrop);
  }
  .card-set {
    width: 1200px;
    height: 900px;
    display: flex;
    flex-direction: column;
    align-items: center;
    justify-content: center;
    gap: 56px;
  }
  .card {
    width: 588px;
    height: 336px;
    border-radius: 3px;
    box-shadow: 0 10px 28px var(--shadow);
    position: relative;
    overflow: hidden;
  }

  /* Company name: one font, one weight, one colour per card */
  .company-name {
    font-family: "Arimo", Helvetica, Arial, sans-serif;
    font-weight: 400;
    line-height: 1.3;
  }

  .card--front {
    background: var(--slate);
    display: flex;
    align-items: center;
    justify-content: center;
  }
  .card--front .company-name {
    color: var(--name-light);
    font-size: 26px;
    text-align: center;
  }

  .card--back {
    background: var(--paper);
    display: grid;
    grid-template-columns: 1fr 1fr;
    align-items: center;
    padding: 0 40px 0 44px;
  }
  .card--back .company-name {
    color: var(--slate-ink);
    font-size: 17px;
    align-self: end;
    margin-bottom: 92px;
  }

  .contact {
    font-family: "Arimo", Helvetica, Arial, sans-serif;
    color: var(--text-grey);
    padding-left: 10px;
  }
  .contact__name {
    font-family: "Cormorant Garamond", Georgia, serif;
    font-weight: 700;
    font-size: 22px;
    letter-spacing: 0.06em;
    text-transform: uppercase;
    color: var(--slate-ink);
  }
  .contact__title { font-size: 13px; margin-top: 2px; }
  .contact__address { font-size: 13px; line-height: 1.45; margin-top: 18px; font-style: normal; }
  .contact__lines { list-style: none; margin-top: 18px; font-size: 13px; line-height: 1.7; }
  .contact__lines li { display: flex; align-items: center; gap: 8px; }
  .contact__icon { width: 11px; height: 11px; flex: none; }
</style>
</head>
<body>
<main class="card-set">
  <section class="card card--front" aria-label="Card front">
    <p class="company-name">Quarrystone<br>Development Group, LLC</p>
  </section>

  <section class="card card--back" aria-label="Card back">
    <p class="company-name">Quarrystone<br>Development Group, LLC</p>
    <div class="contact">
      <h1 class="contact__name">Harlan Vesey</h1>
      <p class="contact__title">Director</p>
      <address class="contact__address">1187 Ledgewood Row<br>Millbrook, OR 97088</address>
      <ul class="contact__lines">
        <li>
          <svg class="contact__icon" viewBox="0 0 12 12" aria-hidden="true"><path d="M3 1 L5 3.5 L4 5 Q5 7 7 8 L8.5 7 L11 9 L9.5 11 Q5 10.5 1 3 Z" fill="currentColor"/></svg>
          (555) 214-3380
        </li>
        <li>
          <svg class="contact__icon" viewBox="0 0 12 12" aria-hidden="true"><rect x="1" y="2.5" width="10" height="7" fill="none" stroke="currentColor" stroke-width="1.1"/><path d="M1 2.5 L6 6.5 L11 2.5" fill="none" stroke="currentColor" stroke-width="1.1"/></svg>
          info@quarrystonegroup.com
        </li>
        <li>
          <svg class="contact__icon" viewBox="0 0 12 12" aria-hidden="true"><circle cx="6" cy="6" r="5" fill="none" stroke="currentColor" stroke-width="1.1"/><ellipse cx="6" cy="6" rx="2.2" ry="5" fill="none" stroke="currentColor" stroke-width="0.9"/><path d="M1 6 H11" stroke="currentColor" stroke-width="0.9"/></svg>
          www.quarrystonegroup.com
        </li>
      </ul>
    </div>
  </section>
</main>
</body>
</html>
```